Fresh Dwelling Tract Guide needs a new Landing Page

I like to get a landing page or website with 2-3 pages to help target home buyers who are looking to buy homes from builders such as TW Residences, Morvik, P.L. Fennick, etc. The landing page/website to be non-cluttered and be able to explain to home buyers that there are many benefits to include me as their buyer's agent when they buy a brand new home from any builders.
I may want to incorporate a short explanation video (animated) on the landing page and then for the viewer to click on a button that will take them to another page where they can search for new homes from different builders.
Target Market(s)
Home buyers looking to buy brand new home from builders such as TW Residences, Morvik, P.L. Fennick, etc.
Industry/Entity Type
Real Estate
Number of Pages Required
2 page
Font styles to use
Requirements
Must have
- The landing page may have the explanation video at the bottom of the landing page (scrolled down) or there may be a CALL TO ACTION button that takes the viewer to the 2nd page to watch the explanation video. Once they watched the explanation video and are still interested, they can click on another CALL TO ACTION button that will take them to another website that they will be able to search for all the available new homes and register their contact information.
Should not have
- No clutters and no dark colors.

```html
<!DOCTYPE html>
<html lang="en">
<head>
<meta charset="utf-8">
<title>Fresh Dwelling Tract Guide</title>
<link rel="stylesheet" href="https://fonts.googleapis.com/css2?family=Poppins:wght@300;400;500;600;700&display=swap">
<style>
  :root {
    --white: #ffffff;
    --cta-red: #cc1e24;
    --cta-red-dark: #a50f15;
    --footer-bg: #111111;
    --hero-top: #d4d5d8;
    --hero-mid: #c2c4c9;
    --hero-low: #b4aea6;
    --hero-floor: #a8947f;
    --text-shade: rgba(40, 42, 48, 0.35);
  }
  * { margin: 0; padding: 0; box-sizing: border-box; }
  html, body { width: 1200px; height: 724px; overflow: hidden; }
  body { font-family: "Poppins", sans-serif; color: var(--white); background: var(--footer-bg); }
  .page { position: relative; width: 1200px; height: 724px; }

  .hero {
    position: absolute; left: 0; top: 0; width: 1200px; height: 669px;
    background:
      radial-gradient(ellipse 60% 45% at 50% 45%, rgba(150,156,168,0.35) 0%, rgba(150,156,168,0) 100%),
      linear-gradient(180deg, var(--hero-top) 0%, var(--hero-mid) 45%, var(--hero-low) 78%, var(--hero-floor) 100%);
  }
  .hero-photo { position: absolute; inset: 0; }

  .site-header { position: absolute; left: 0; top: 0; width: 1200px; height: 110px; }
  .brand { position: absolute; left: 96px; top: 22px; display: flex; align-items: center; gap: 14px; }
  .brand-mark { width: 62px; height: 62px; border-radius: 50%; background: var(--white); }
  .brand-name { font-size: 31px; font-weight: 600; letter-spacing: -0.3px; line-height: 1; text-shadow: 0 1px 6px var(--text-shade); }
  .menu-toggle { position: absolute; left: 1034px; top: 48px; width: 19px; height: 17px; display: flex; flex-direction: column; justify-content: space-between; }
  .menu-toggle span { display: block; height: 3px; background: var(--white); }

  .hero-text { position: absolute; left: 0; width: 1200px; text-align: center; text-shadow: 0 2px 10px var(--text-shade); white-space: nowrap; }
  .hero-kicker { top: 245px; font-size: 45px; font-weight: 300; line-height: 58px; }
  .hero-title { top: 300px; font-size: 62px; font-weight: 600; line-height: 84px; letter-spacing: -0.5px; }
  .watch-video { top: 390px; display: flex; justify-content: center; align-items: center; gap: 12px; font-size: 28px; font-weight: 400; line-height: 38px; }
  .watch-video svg { width: 26px; height: 26px; }

  .cta-button {
    position: absolute; left: 455px; top: 450px; width: 291px; height: 67px; line-height: 67px; border-radius: 34px;
    background: linear-gradient(180deg, var(--cta-red) 0%, var(--cta-red-dark) 100%);
    text-align: center; font-size: 16.5px; font-weight: 600; color: var(--white); text-decoration: none;
    box-shadow: 0 3px 10px rgba(90, 10, 12, 0.25);
  }

  .slider-dots { position: absolute; left: 0; width: 1200px; top: 631px; display: flex; justify-content: center; align-items: center; gap: 11px; }
  .slider-dots span { width: 9px; height: 9px; border-radius: 50%; background: var(--white); }
  .slider-dots .active { box-shadow: 0 0 0 3px rgba(0,0,0,0.12), 0 0 0 4px var(--white); }

  .site-footer { position: absolute; left: 0; top: 669px; width: 1200px; height: 55px; background: var(--footer-bg); display: flex; align-items: center; justify-content: center; font-size: 13px; font-weight: 500; }
</style>
</head>
<body>
<div class="page">
  <section class="hero">
    <div class="hero-photo" role="img" aria-label="Photo of a bright open-plan dining room and living area in a new home"></div>
    <header class="site-header">
      <div class="brand">
        <span class="brand-mark"></span>
        <span class="brand-name">Fresh Dwelling Tract Guide</span>
      </div>
      <div class="menu-toggle" aria-label="Menu"><span></span><span></span><span></span></div>
    </header>
    <p class="hero-text hero-kicker">Welcome to</p>
    <h1 class="hero-text hero-title">Fresh Dwelling Tract Guide</h1>
    <div class="hero-text watch-video">
      <svg viewBox="0 0 26 26" aria-hidden="true"><circle cx="13" cy="13" r="13" fill="#fff"/><path d="M10 7.5 L19 13 L10 18.5 Z" fill="#8a8c93"/></svg>
      <span>Watch Video</span>
    </div>
    <a class="cta-button" href="#">FIND YOUR DREAM HOUSE</a>
    <div class="slider-dots"><span class="active"></span><span></span><span></span><span></span></div>
  </section>
  <footer class="site-footer">Copyright © 2018. All Rights Reserved.</footer>
</div>
</body>
</html>
```